Verodex business card

Business card for sustainable investment company called "Verodex". Verodex is an exchange platform selling carbon credits between buyers and sellers. Carbon Credits are an environmental commodity for reducing global carbon emissions.

the card should obviously have our logo and the theme should be sustainability/environment mixed with a trading platform.

Contact Information for Business Card

Logo, Name, Title, Phone, Email

Colors
0054AA
0677BA
7BADD7
CADEEF
E8F1F8
0094D4
00A9DD
6FCCEA
C7EBF8
E9F6FB
00AB8E
00BBA5
67D7C9
C6EFE9
E9F9F6
59FF00
82FF00
B8FF75
E3FFCB
F4FFEA

```html
<!DOCTYPE html>
<html lang="en">
<head>
<meta charset="utf-8">
<title>Verodex business card</title>
<link rel="stylesheet" href="https://fonts.googleapis.com/css2?family=Archivo+Narrow:wght@400;700&family=Archivo:wght@700;800&family=Montserrat:wght@700&display=swap">
<style>
  :root {
    --backdrop: #cadeef;
    --card: #e9f9f6;
    --card-edge: #c6efe9;
    --frame: #00ab8e;
    --ink: #0054aa;
    --ink-soft: #0677ba;
    --accent: #00a9dd;
    --leaf: #59ff00;
  }
  * { margin: 0; padding: 0; box-sizing: border-box; }
  html, body { width: 1200px; height: 976px; overflow: hidden; }
  body {
    background: var(--backdrop);
    position: relative;
    font-family: "Archivo", Arial, sans-serif;
    color: var(--ink);
  }
  .card {
    position: absolute;
    background: var(--card);
    box-shadow: 0 2px 0 var(--card-edge), 0 18px 36px rgba(0, 84, 170, .18);
  }
  .card-frame {
    position: absolute;
    inset: 16px;
    border: 6px solid var(--frame);
  }

  /* Contact side (portrait) */
  .card--contact { left: 180px; top: 225px; width: 300px; height: 525px; }
  .contact-body {
    position: absolute; inset: 16px;
    display: flex; flex-direction: column; align-items: center;
    padding-top: 70px; text-align: center;
  }
  .brand-small {
    display: flex; align-items: center; gap: 8px;
    font-family: "Archivo", Arial, sans-serif;
    font-weight: 800; font-size: 20px; letter-spacing: 2px;
    color: var(--ink);
  }
  .brand-dot { width: 12px; height: 12px; border-radius: 50%; background: var(--frame); }
  .person-name {
    margin-top: 38px;
    font-family: "Archivo Narrow", "Arial Narrow", sans-serif;
    font-weight: 700; font-size: 38px; line-height: 1; letter-spacing: .5px;
    color: var(--ink);
  }
  .person-title {
    margin-top: 4px;
    font-family: "Archivo Narrow", "Arial Narrow", sans-serif;
    font-weight: 400; font-size: 19px;
    color: var(--ink-soft);
  }
  .icon-row {
    margin-top: 26px;
    display: flex; align-items: center; gap: 12px;
  }
  .icon-row .dash { width: 18px; height: 4px; background: var(--frame); }
  .icon-row svg { width: 18px; height: 18px; }
  .contact-list {
    margin-top: 26px; list-style: none;
    font-family: "Archivo", Arial, sans-serif; font-weight: 700;
    color: var(--ink);
  }
  .contact-list .phone { font-size: 24px; letter-spacing: 1px; }
  .contact-list .line { font-size: 15px; letter-spacing: .8px; margin-top: 4px; color: var(--ink-soft); }

  /* Brand side (landscape) */
  .card--brand { left: 540px; top: 338px; width: 525px; height: 300px; background: var(--ink); box-shadow: 0 2px 0 #003f80, 0 18px 36px rgba(0, 84, 170, .22); }
  .card--brand .card-frame { border-color: var(--accent); }
  .brand-body {
    position: absolute; inset: 16px;
    display: flex; align-items: center; justify-content: center; gap: 18px;
  }
  .brand-square { width: 40px; height: 40px; background: var(--leaf); }
  .brand-large {
    font-family: "Montserrat", Arial, sans-serif;
    font-weight: 700; font-size: 56px; letter-spacing: 2px;
    color: #e9f6fb;
  }
</style>
</head>
<body>

<section class="card card--contact" aria-label="Card contact side">
  <div class="card-frame"></div>
  <div class="contact-body">
    <div class="brand-small"><span class="brand-dot"></span>VERODEX</div>
    <h1 class="person-name">MARCUS HALE</h1>
    <p class="person-title">Founder &amp; CEO</p>
    <div class="icon-row">
      <span class="dash"></span>
      <svg viewBox="0 0 24 24" aria-label="Phone"><path fill="#0054aa" d="M6.6 10.8a15 15 0 0 0 6.6 6.6l2.2-2.2c.3-.3.7-.4 1-.2 1.1.4 2.3.6 3.6.6.6 0 1 .4 1 1V20c0 .6-.4 1-1 1A17 17 0 0 1 3 4c0-.6.4-1 1-1h3.5c.6 0 1 .4 1 1 0 1.3.2 2.5.6 3.6.1.3 0 .7-.2 1z"/></svg>
      <svg viewBox="0 0 24 24" aria-label="Email"><rect x="2" y="5" width="20" height="14" rx="1.5" fill="#0054aa"/><path d="M3 6l9 7 9-7" stroke="#e9f9f6" stroke-width="1.6" fill="none"/></svg>
      <svg viewBox="0 0 24 24" aria-label="Website"><circle cx="12" cy="12" r="9.5" fill="none" stroke="#0054aa" stroke-width="2.4"/><ellipse cx="12" cy="12" rx="4" ry="9.5" fill="none" stroke="#0054aa" stroke-width="2"/><path d="M3 12h18" stroke="#0054aa" stroke-width="2"/></svg>
      <span class="dash"></span>
    </div>
    <ul class="contact-list">
      <li class="phone">(555) 284-6190</li>
      <li class="line">OFFICE@VERODEX.COM</li>
      <li class="line">WWW.VERODEX.COM</li>
    </ul>
  </div>
</section>

<section class="card card--brand" aria-label="Card brand side">
  <div class="card-frame"></div>
  <div class="brand-body">
    <span class="brand-square"></span>
    <span class="brand-large">VERODEX</span>
  </div>
</section>

</body>
</html>
```